White Paper and One-Page Advertisement for TELVORISH-QM

I need both documents to be better formatted and designed so they look professional, not something someone with mediocre word skills put together. They will go out to 1000s of industry professionals, and they need to look sharp. I need them to have my company's color palate logo, and branding on it similar to how it is now, but better. Please do not change any of the written content, but it can be arranged in any other format you think is better. Smart art and things i've already used can be omitted in favor of better designs. The developer is free to use their creativity. White paper should not be longer than the three pages unless necessary.

Target Market(s)

Life Sciences supply chain professionals

Colors
33b8a4
0592cd
9bcb3c
fbee3e
3277b5

Requirements
Must have
• Must be professional looking and not look like something done in word. Please use the color palate as seen on the documents.
Should not have
• Any changes to the written content.

```html
<!DOCTYPE html>
<html lang="en">
<head>
<meta charset="utf-8">
<title>White Paper Spread</title>
<link rel="stylesheet" href="https://fonts.googleapis.com/css2?family=Roboto+Condensed:wght@400;700&family=Arimo:wght@400;700&display=swap">
<style>
:root{
  --teal:#33b8a4;
  --blue:#0592cd;
  --green:#9bcb3c;
  --yellow:#fbee3e;
  --navy:#3277b5;
  --lime:#c9db2e;
  --cyan:#2fb8d6;
  --ink:#3a3d40;
  --panel:#5aaec0;
  --stage:#e9ecee;
}
*{box-sizing:border-box;margin:0;padding:0}
html,body{width:1200px;height:900px;overflow:hidden;background:var(--stage)}
body{position:relative;font-family:"Arimo",Arial,sans-serif;color:var(--ink)}
.page{position:absolute;top:98px;width:496px;height:702px;background:#fff;overflow:hidden}
.page--left{left:82px}
.page--right{left:622px}
.page__wash{position:absolute;left:0;top:0;width:100%;height:100%;background:linear-gradient(160deg,#eef3df 0%,#e6f3f5 22%,#ffffff 45%,#ffffff 100%)}
.page__chevron{position:absolute;left:0;top:0;width:100%;height:100%}
.col{position:absolute;font-size:8.6px;line-height:11.2px}
.col p{text-align:justify}
.h-cond{font-family:"Roboto Condensed",Arial Narrow,sans-serif;font-weight:700;color:var(--blue);font-size:11px;text-transform:uppercase;letter-spacing:.1px}
.h-light{color:var(--blue);font-size:11px}
.h-sub{font-size:11px;color:var(--ink)}
.bullets{list-style:none}
.bullets li{position:relative;padding-left:10px;margin-bottom:1.2px}
.bullets li::before{content:"";position:absolute;left:0;top:2.5px;width:6px;height:6px;border:1px solid var(--blue);border-radius:50%;background:radial-gradient(circle,var(--blue) 0 1.3px,transparent 1.6px)}
.abs{position:absolute}
.donut{position:absolute;left:270px;top:142px;width:180px;height:180px}
.barriers{position:absolute;left:24px;top:239px;width:448px;height:279px;background:var(--panel)}
.barriers__head{height:35px;background:var(--green);color:#fff;font-family:"Roboto Condensed",sans-serif;font-weight:700;font-size:14px;text-align:center;line-height:35px}
.barrier{position:absolute;width:210px}
.barrier__arrow{display:block;width:210px;height:28px}
.barrier__title{position:absolute;left:9px;top:7px;color:#fff;font-family:"Roboto Condensed",sans-serif;font-weight:700;font-size:11px}
.barrier__text{color:#fff;font-size:8.2px;line-height:10.2px;text-align:justify;padding:3px 8px 0 14px}
</style>
</head>
<body>

<section class="page page--left">
  <div class="page__wash" role="img" aria-label="Soft geometric triangle texture in pale green and aqua"></div>
  <svg class="page__chevron" viewBox="0 0 496 702" preserveAspectRatio="none" aria-hidden="true">
    <defs>
      <linearGradient id="chevL" x1="0" y1="0" x2="0" y2="1">
        <stop offset="0" stop-color="#bfe3ea"/><stop offset="1" stop-color="#5fb6c9"/>
      </linearGradient>
    </defs>
    <polygon points="0,514 190,702 0,702" fill="#d8eef2"/>
    <polygon points="496,394 496,702 190,702" fill="url(#chevL)"/>
    <polygon points="0,514 190,702 496,394 496,470 190,702 0,560" fill="#8fd0dd" opacity=".45"/>
  </svg>

  <div class="col" style="left:35px;top:38px;width:205px">
    <ul class="bullets">
      <li>High CoGS due to materials write-downs</li>
      <li>High inventory carrying costs</li>
      <li>Greater business continuity risk</li>
      <li>High Disposal costs</li>
      <li>Larger environmental footprint</li>
      <li>Stock-out materials</li>
    </ul>
  </div>
  <div class="col" style="left:35px;top:114px;width:205px">
    <div class="h-light">Who?</div>
    <ul class="bullets" style="margin-top:4px"><li style="text-align:justify">FDA Regulated Industries, Procurement, Quality, Production, and Finance.</li></ul>
  </div>
  <div class="col" style="left:35px;top:158px;width:205px">
    <div class="h-light">Where and When?</div>
    <ul class="bullets" style="margin-top:4px">
      <li style="text-align:justify;margin-bottom:4px">Commercial &amp; clinical production, R&amp;D, sourcing/purchasing, production planning, quality testing, etc.</li>
      <li style="text-align:justify">Volatile demand periods, e.g., product intro growth, decline, seasonality, economic uncertainty, and unforeseen events.</li>
    </ul>
  </div>
  <div class="col" style="left:35px;top:249px;width:205px">
    <div class="h-light">How do we know it's there?</div>
    <ul class="bullets" style="margin-top:4px"><li>We physically see it taking place, and it's in our data.</li></ul>
  </div>
  <div class="col" style="left:35px;top:303px;width:205px">
    <div class="h-cond">Triple Bottom Line Impact</div>
    <div class="h-light" style="margin-top:8px">Financial</div>
    <div class="h-sub" style="margin-top:6px">Vendors/Sellers</div>
    <ul class="bullets" style="margin-top:4px"><li>Higher write-downs/offs and 3rd party disposal fees</li></ul>
    <div class="h-sub" style="margin-top:6px">Buyers</div>
    <ul class="bullets" style="margin-top:4px">
      <li>Lost sales - stock-outs</li>
      <li style="text-align:justify">Inflated market value of materials &amp; supplier expedition fees</li>
      <li>High SS cost due to bullwhip effect</li>
    </ul>
    <div class="h-sub" style="margin-top:10px">Environment</div>
    <ul class="bullets" style="margin-top:4px">
      <li style="text-align:justify">Greater contribution to global warming through landfill addition, incineration, inactivation, and energy consumption</li>
      <li>Non compliance with ISO 14000 &amp; 9000 and B-Corp Status</li>
    </ul>
    <div class="h-sub" style="margin-top:6px">Society</div>
    <ul class="bullets" style="margin-top:4px">
      <li style="text-align:justify">Lost community trust - high environment and consumer costs.</li>
      <li>Less innovation, collaboration, and supply chain optimization</li>
    </ul>
  </div>

  <div class="col" style="left:258px;top:32px;width:205px">
    <div class="h-cond">Current State</div>
    <div class="h-cond" style="margin-top:8px">External Solutions</div>
    <p style="margin-top:6px">Pharma and other FDA industries spend considerable energy on reducing waste. A plethora of techniques are employed to mitigate, prepare for, respond to, and recover from the bullwhip effect, which is one of the leading causes of write-downs and waste. However, such efforts are predicated on:</p>
  </div>

  <svg class="donut" viewBox="-90 -90 180 180" role="img" aria-label="Bullwhip influences ring chart">
    <defs>
      <path id="arcTL" d="M-62.04,-10.94 A63 63 0 0 1 -10.94,-62.04"/>
      <path id="arcTR" d="M10.94,-62.04 A63 63 0 0 1 62.04,-10.94"/>
      <path id="arcBR" d="M62.04,10.94 A63 63 0 0 1 10.94,62.04"/>
      <path id="arcBL" d="M-10.94,62.04 A63 63 0 0 1 -62.04,10.94"/>
    </defs>
    <path d="M-79.95,-2.79 A80 80 0 0 1 -2.79,-79.95 L-1.61,-45.97 A46 46 0 0 0 -45.97,-1.61 Z" fill="var(--green)"/>
    <path d="M2.79,-79.95 A80 80 0 0 1 79.95,-2.79 L45.97,-1.61 A46 46 0 0 0 1.61,-45.97 Z" fill="var(--lime)"/>
    <path d="M79.95,2.79 A80 80 0 0 1 2.79,79.95 L1.61,45.97 A46 46 0 0 0 45.97,1.61 Z" fill="var(--cyan)"/>
    <path d="M-2.79,79.95 A80 80 0 0 1 -79.95,2.79 L-45.97,1.61 A46 46 0 0 0 -1.61,45.97 Z" fill="var(--teal)"/>
    <g font-family="Roboto Condensed, sans-serif" font-weight="700" font-size="7" fill="#fff" text-anchor="middle">
      <text dy="2.5"><textPath href="#arcTL" startOffset="50%">FORECAST ACCURACY</textPath></text>
      <text dy="2.5"><textPath href="#arcTR" startOffset="50%">SUPPLIER RELIABILITY</textPath></text>
      <text dy="2.5"><textPath href="#arcBR" startOffset="50%">EXTERNAL ENVIRONMENT</textPath></text>
      <text dy="2.5"><textPath href="#arcBL" startOffset="50%">PROCESS VARIABILITY</textPath></text>
    </g>
    <g font-family="Roboto Condensed, sans-serif" font-weight="700" font-size="13" fill="var(--blue)" text-anchor="middle">
      <text y="-2">BULLWHIP</text>
      <text y="13">INFLUENCES</text>
    </g>
  </svg>

  <div class="col" style="left:258px;top:313px;width:205px">
    <p>While not fruitless, attempts to mitigate the above external influences are extremely unpredictable and have never solved pharma's write-down, inefficiency, stock-out, and environmental problems.</p>
    <div class="h-cond" style="margin-top:10px">Internal Solutions</div>
    <p style="margin-top:5px">The next effort involves reducing obsolence by making use of materials within the firm. Typically, interplant demand is the only outlet to optimize surplus earmarked for a reserve/write-down. Even this involves may of the same regulatory compliance, quality, and economic challenges. Facilitating this takes time, resources, and does not provide a broad network to utilize.</p>
    <div class="h-cond" style="margin-top:14px">Environmental Solutions</div>
    <p style="margin-top:5px">FDA industries, like most others, make attempts to reuse, recycle, and convert to energy where applicable. However, they're unable to conduct these activities for perishable, expiring, and/or consumable materials.</p>
    <div class="h-cond" style="margin-top:14px">Undesirable Solutions</div>
    <p style="margin-top:5px">Unfortunately, third party disposal (frequently landfill) is typically the first and most popular option as perishable, expiring, and complex materials are generally unable to be reused or recycled. These disposals come in many forms to include responsible landfills, incinceration, inactivation, etc.</p>
  </div>
</section>

<section class="page page--right">
  <div class="page__wash" role="img" aria-label="Soft geometric triangle texture in pale green and aqua"></div>
  <svg class="page__chevron" viewBox="0 0 496 702" preserveAspectRatio="none" aria-hidden="true">
    <defs>
      <linearGradient id="chevR" x1="0" y1="0" x2="0" y2="1">
        <stop offset="0" stop-color="#bfe3ea"/><stop offset="1" stop-color="#5fb6c9"/>
      </linearGradient>
    </defs>
    <polygon points="0,414 186,702 0,702" fill="#d8eef2"/>
    <polygon points="496,394 496,702 186,702" fill="url(#chevR)"/>
  </svg>

  <div class="col" style="left:34px;top:36px;width:205px">
    <div class="h-cond">Overall</div>
    <p style="margin-top:6px">Industries spend much capital and resources to reduce write-downs in an environment where the bullwhip effect reigns supreme. Mitigations to this effect are attempted but only partially successful or sustainable.</p>
    <div class="h-cond" style="margin-top:8px">Refined Problem</div>
    <p style="margin-top:5px">There is no clear market leader that helps organizations optimize waste, collaborative to reduce it, and market more quality materials to more firms whether for research, manufacturing, or donations. This marketplace must be regulated and all participates properly vetted and authenticated. Accounts must be created to enable companies to post materials and request for information/quotes. Additionally, this marketplace must facilitate</p>
  </div>
  <div class="col" style="left:258px;top:37px;width:205px">
    <p>collaborative relationships between companies thathelp them reduce supply chain costs. It must quickly, economically, compliantly, and legally facilitatethose exchanges. Lack of this market leader may have enabled the waste problem as seen today.</p>
    <div class="h-light" style="margin-top:8px">Contemporary Operating Environment</div>
    <ul class="bullets" style="margin-top:5px">
      <li style="text-align:justify">Constant pressure from global competition, increasing customer and governmental demand on price, more regulatory scrutiny, and a relentless societal pursuit of sustainability are starting to erode what were once high margins for Pharma.</li>
      <li>Regulators are cooperative and open to solutions.</li>
      <li style="text-align:justify">Exchanges and consortiums are not typically leveraged in Pharma.</li>
      <li style="text-align:justify">Pharma continues to struggle with the bullwhip effect.</li>
    </ul>
  </div>

  <div class="barriers">
    <div class="barriers__head">BARRIERS</div>

    <div class="barrier" style="left:6px;top:43px">
      <svg class="barrier__arrow" viewBox="0 0 210 28" aria-hidden="true"><polygon points="0,0 190,0 210,14 190,28 0,28" fill="var(--green)"/></svg>
      <span class="barrier__title">COMPLIANCE</span>
      <p class="barrier__text">It is the responsibility of manufacturers to provide customers/patients with quality, safe, and efficacious products. However, there is a misperception that high quality cGMP compliant materials, parts, and equipment cannot be sourced from aftermarket exchanges and consortiums.</p>
    </div>
    <div class="barrier" style="left:231px;top:43px">
      <svg class="barrier__arrow" viewBox="0 0 210 28" aria-hidden="true"><polygon points="0,0 190,0 210,14 190,28 0,28" fill="var(--lime)"/></svg>
      <span class="barrier__title">LIABILITY</span>
      <p class="barrier__text">Contractual agreements with suppliers have clauses to resolve issues dealing with poor quality. There is a misperception that these agreements cannot implemented at both the marketplace and transactional level.</p>
    </div>
    <div class="barrier" style="left:6px;top:143px">
      <svg class="barrier__arrow" viewBox="0 0 210 28" aria-hidden="true"><polygon points="0,0 190,0 210,14 190,28 0,28" fill="#129a86"/></svg>
      <span class="barrier__title">ECONOMICS</span>
      <p class="barrier__text">Exchanges can be difficult due to time/effort. A sanctioned marketplace can provide the structure to make it easy.</p>
    </div>
    <div class="barrier" style="left:231px;top:143px">
      <svg class="barrier__arrow" viewBox="0 0 210 28" aria-hidden="true"><polygon points="0,0 190,0 210,14 190,28 0,28" fill="#8fd3e2"/></svg>
      <span class="barrier__title">SUSTAINABILITY</span>
      <p class="barrier__text">Firms have not discovered how to leverage exchanges to reduce environmental footprint and enable industry certifications as well as community trust.</p>
    </div>
    <div class="barrier" style="left:6px;top:215px">
      <svg class="barrier__arrow" viewBox="0 0 210 28" aria-hidden="true"><polygon points="0,0 190,0 210,14 190,28 0,28" fill="var(--blue)"/></svg>
      <span class="barrier__title">CONFIDENCE</span>
      <p class="barrier__text">Trust is critical to firms. They should know that a marketplace has properly vetted members with KPI data for analysis.</p>
    </div>
    <div class="barrier" style="left:231px;top:215px">
      <svg class="barrier__arrow" viewBox="0 0 210 28" aria-hidden="true"><polygon points="0,0 190,0 210,14 190,28 0,28" fill="#8cc43e"/></svg>
      <span class="barrier__title">SPEED</span>
      <p class="barrier__text">Exchanges should be fast. An innovative marketplace can ensure quick exchanges.</p>
    </div>
  </div>

  <div class="col" style="left:34px;top:532px;width:205px">
    <div class="h-cond">Root Cause &amp; Paradigm Shift</div>
    <p style="margin-top:5px">Comfort in the status quo has enabled a culture of waste. With life science margins so high, it hasn't been a priority to solve. Additionally, there hasn't been an effective means to deal with waste. This limits the industry's ability to leverage these marketplaces. Finally, misperceived issues or liability and quality have strained innovation; all solvable problems.</p>
    <div class="h-light" style="margin-top:10px">Future State</div>
    <p style="margin-top:5px">Creation of Private Virtual Life Sciences Multi-Vendor Marketplace &amp; Consortiumwhere researchers,</p>
  </div>
  <div class="col" style="left:258px;top:532px;width:205px">
    <p>manufacturers, and original-end manufacturers can create a simple storefront for their organization and transact materials, equipment, parts, and collaborative relationships in a compliant and professional environment. This marketplace uses a series of software logic that leverages auditing capabilities of buyers and sellers by making FDA required data and documentation visible and subject to ALCOA-Plus, thus enabling transactions in a fast and compliant manner. This logic then automates contracts for digital signature in a part 11 compliant package.</p>
  </div>
</section>

</body>
</html>
```